We would like to have one website and the similar (or the same) Facebook site.
We need only the first website without sub-pages and menus. We are preparing a new product for the market. On the page should be the logo, company data, few pictures and the text about our product.
The company color is red.
Company data are Korvelt GmbH, CH-4417 Ermendorf, Switzerland, media@korvelt.example, www.korvelt.example.
Text for the page:
"We are Swiss engineers with many years of experience in ultra-precision electronics.
We develop the TidoBand, a smartwatch that can save lives. It is designed for elderly people who live alone and want to maintain their independence longer, without fear.
Our TidoBand will be available at 4th quarter of 2018."

```html
<!DOCTYPE html>
<html lang="en">
<head>
<meta charset="utf-8">
<title>Korvelt TidoBand</title>
<link href="https://fonts.googleapis.com/css2?family=Oswald:wght@500&family=Roboto:wght@400;500;700&display=swap" rel="stylesheet">
<style>
:root{
  --red:#e8262d;
  --red-band:#e5343b;
  --grey-text:#6f6f6f;
  --dark:#222222;
  --body:#444444;
  --light-bg:#f2f2f2;
  --nav-grey:#6e6e6e;
  --white:#ffffff;
  --watch-dark:#333333;
}
*{box-sizing:border-box;margin:0;padding:0}
html,body{width:1200px;height:2586px;overflow:hidden}
body{position:relative;font-family:"Roboto",Arial,sans-serif;color:var(--body);background:var(--white)}
.abs{position:absolute}

/* Hero */
.hero{position:absolute;left:0;top:0;width:1200px;height:638px;overflow:hidden}
.hero-photo{position:absolute;inset:0;background:linear-gradient(100deg,#6f8fa8 0%,#8aa0a8 30%,#b9a89a 55%,#d9b6a6 75%,#9aa7a4 100%)}
.brand{position:absolute;font-family:"Roboto",Arial,sans-serif;font-weight:700;font-size:46px;color:var(--red);letter-spacing:-0.5px}
.hero .brand{left:98px;top:38px}
.main-nav{position:absolute;left:505px;top:43px;height:46px;width:595px;background:var(--nav-grey);border-radius:23px;display:flex;overflow:hidden}
.main-nav a{display:flex;align-items:center;justify-content:center;white-space:nowrap;color:var(--white);font-size:14px;font-weight:500;text-decoration:none;letter-spacing:.2px;border-right:1px solid rgba(255,255,255,.25)}
.main-nav a:nth-child(1){width:86px}
.main-nav a:nth-child(2){width:100px}
.main-nav a:nth-child(3){width:119px}
.main-nav a:nth-child(4){width:148px}
.main-nav a:nth-child(5){width:142px;border-right:none}
.main-nav a.active{background:var(--red);border-radius:23px 0 0 23px}
.hero-title{position:absolute;left:98px;top:214px;font-family:"Oswald",Arial,sans-serif;font-weight:500;font-size:52px;line-height:56px;color:var(--white);text-transform:uppercase}
.btn{display:inline-flex;align-items:center;justify-content:center;background:var(--red);color:var(--white);font-weight:700;font-size:14px;text-transform:uppercase;border-radius:3px;text-decoration:none}
.hero .btn{position:absolute;left:98px;top:401px;width:120px;height:34px}
.slider-dots{position:absolute;left:589px;top:584px;display:flex;gap:8px}
.slider-dots span{width:18px;height:18px;border-radius:50%;border:2px solid var(--white)}
.slider-dots span.on{background:var(--white)}

/* Welcome */
.welcome{position:absolute;left:0;top:638px;width:1200px;height:470px;background:var(--light-bg)}
.welcome-photo{position:absolute;left:101px;top:70px;width:340px;height:340px;border-radius:50%;border:6px solid #7a7a7a;background:radial-gradient(circle at 45% 45%,#e7d4c4,#b7b3b4 70%,#8c98a6)}
.welcome-watch{position:absolute;left:320px;top:264px;width:140px;height:140px;border-radius:50%;background:radial-gradient(circle,#555 0%,var(--watch-dark) 70%);border:4px solid var(--light-bg)}
.welcome-copy{position:absolute;left:502px;top:72px;width:600px}
.welcome-copy h2{font-size:34px;line-height:40px;font-weight:700;text-transform:uppercase;color:var(--red)}
.welcome-copy h2 span{display:block;color:var(--grey-text);font-weight:500}
.welcome-copy p{font-size:13px;line-height:22px;color:var(--body);margin-top:14px}
.welcome-copy .btn{width:170px;height:38px;margin-top:20px;font-size:14px}

/* Features */
.features{position:absolute;left:0;top:1108px;width:1200px;height:699px;background:var(--white)}
.section-title{position:absolute;left:0;width:1200px;text-align:center;font-size:34px;font-weight:700;text-transform:uppercase;color:var(--red)}
.section-title span{color:var(--grey-text);font-weight:500}
.features .section-title{top:72px}
.features-intro{position:absolute;left:300px;top:124px;width:600px;text-align:center;font-size:12.5px;line-height:22px;color:var(--body)}
.feature{position:absolute;width:280px}
.feature h3{font-size:17px;font-weight:500;text-transform:uppercase;color:var(--dark);letter-spacing:.3px}
.feature p{font-size:12.5px;line-height:21px;margin-top:10px;color:var(--body)}
.feature.left{text-align:right}
.feature-icon{position:absolute}

/* Reviews */
.reviews{position:absolute;left:0;top:1807px;width:1200px;height:420px;overflow:hidden}
.reviews-bg{position:absolute;inset:0;background:var(--red-band)}
.reviews .section-title{top:58px;color:var(--white);font-weight:500;font-size:32px}
.title-rule{position:absolute;left:570px;top:114px;width:60px;height:2px;background:var(--white)}
.review{position:absolute;top:168px;width:500px}
.review-avatar{position:absolute;left:0;top:8px;width:124px;height:124px;border-radius:50%;border:4px solid var(--white);background:linear-gradient(135deg,#9bb08a,#d8b8a0 60%,#8ca3b8)}
.review-text{position:absolute;left:145px;top:8px;width:320px;color:var(--white);font-size:12.5px;line-height:20px}
.review-name{position:absolute;left:145px;top:90px;color:var(--white);font-size:13px;text-transform:uppercase}
.review-stars{position:absolute;left:145px;top:118px;color:var(--white);font-size:15px;letter-spacing:3px}
.reviews-wave{position:absolute;left:0;top:340px}

/* Footer */
.site-footer{position:absolute;left:0;top:2207px;width:1200px;height:310px;background:var(--light-bg)}
.site-footer .brand{left:103px;top:96px;font-size:40px}
.social{position:absolute;left:100px;top:162px;display:flex;gap:6px}
.social span{width:30px;height:30px;border-radius:50%;border:1.5px solid #8a8a8a}
.footer-col{position:absolute;top:74px}
.footer-col h4{font-size:20px;font-weight:500;text-transform:uppercase;color:var(--dark);letter-spacing:.3px}
.contact-list{list-style:none;margin-top:22px;font-size:13px;line-height:20px;color:var(--dark)}
.contact-list li{display:flex;gap:14px;margin-bottom:14px}
.contact-list svg{flex:none;margin-top:3px}
.newsletter p{font-size:11.5px;line-height:19px;color:var(--body);margin-top:20px;width:230px}
.newsletter .field{margin-top:14px;width:298px;height:42px;background:var(--white);border:1px solid #d6d6d6;font-size:11.5px;color:#777;display:flex;align-items:center;padding-left:14px}
.newsletter .btn{margin-top:12px;width:122px;height:38px;border-radius:0;font-size:15px}
.quick-links{list-style:none;margin-top:20px;font-size:12.5px;color:var(--dark)}
.quick-links li{line-height:24px}
.quick-links li::before{content:"›";margin-right:12px;font-weight:700}
.copyright{position:absolute;left:0;top:2517px;width:1200px;height:69px;background:var(--white);border-top:1px solid #e0e0e0;display:flex;align-items:center;justify-content:center;font-size:12.5px;color:var(--dark)}
</style>
</head>
<body>

<header class="hero">
  <div class="hero-photo" role="img" aria-label="Photo of a smiling senior woman wearing a smartwatch, leaning on a railing by a lake"></div>
  <div class="brand">Korvelt</div>
  <nav class="main-nav">
    <a class="active" href="#">HOME</a>
    <a href="#">FEATURE</a>
    <a href="#">PRODUCTS</a>
    <a href="#">ABOUT KORVELT</a>
    <a href="#">CONTACT US</a>
  </nav>
  <h1 class="hero-title">Changing the way<br>elderly people<br>stay connected</h1>
  <a class="btn" href="#">Read more</a>
  <div class="slider-dots"><span class="on"></span><span></span><span></span></div>
</header>

<section class="welcome">
  <div class="welcome-photo" role="img" aria-label="Photo of a young woman and her smiling grandfather"></div>
  <div class="welcome-watch" role="img" aria-label="Product photo of the TidoBand smartwatch"></div>
  <div class="welcome-copy">
    <h2>Welcome to<span>Korvelt TidoBands</span></h2>
    <p>We are Swiss engineers with many years of experience in ultra-precision electronics. We develop the TidoBand, a smartwatch that can save lives. It is designed for elderly people who live alone and want to maintain their independence longer, without fear.</p>
    <p>Our TidoBand will be available at 4th quarter of 2018.</p>
    <a class="btn" href="#">Book online here</a>
  </div>
</section>

<section class="features">
  <h2 class="section-title">Korvelt <span>Features</span></h2>
  <p class="features-intro">The TidoBand is a smartwatch that can save lives, made for elderly people<br>who live alone and want to stay independent longer, without fear.</p>

  <svg class="abs" style="left:0;top:0" width="1200" height="699" viewBox="0 0 1200 699">
    <g stroke="#e8262d" stroke-width="3" stroke-dasharray="9 6" fill="none">
      <circle cx="600" cy="409" r="168"/>
      <line x1="408" y1="280" x2="480" y2="320"/>
      <line x1="352" y1="415" x2="432" y2="415"/>
      <line x1="410" y1="546" x2="480" y2="505"/>
      <line x1="792" y1="280" x2="720" y2="320"/>
      <line x1="850" y1="413" x2="768" y2="413"/>
      <line x1="790" y1="546" x2="720" y2="505"/>
    </g>
  </svg>
  <div class="abs" role="img" aria-label="Product photo of two TidoBand smartwatches" style="left:466px;top:275px;width:268px;height:268px;border-radius:50%;background:radial-gradient(circle at 50% 45%,#4a4a4a,#333 75%)"></div>

  <div class="feature left" style="left:54px;top:232px"><h3>Voice calling</h3><p>Sed ut perspiciatis unde omnis iste natus<br>error sit voluptatem accusantium</p></div>
  <div class="feature left" style="left:0;top:372px"><h3>Messaging</h3><p>Sed ut perspiciatis unde omnis<br>iste natus error sit</p></div>
  <div class="feature left" style="left:54px;top:514px"><h3>Safezones</h3><p>Sed ut perspiciatis unde omnis iste natus<br>error sit voluptatem accusantium</p></div>
  <div class="feature" style="left:881px;top:232px"><h3>Intelligent emergency</h3><p>Sed ut perspiciatis unde omnis iste<br>natus error sit voluptatem accusantium</p></div>
  <div class="feature" style="left:926px;top:378px"><h3>Smart locator</h3><p>Sed ut perspiciatis unde omnis<br>iste natus error sit voluptatem</p></div>
  <div class="feature" style="left:864px;top:514px"><h3>Mobile app</h3><p>Sed ut perspiciatis unde omnis iste<br>natus error sit voluptatem accusantium</p></div>

  <svg class="feature-icon" style="left:364px;top:248px" width="34" height="34" viewBox="0 0 24 24"><path fill="#e8262d" d="M6.6 10.8a15.1 15.1 0 0 0 6.6 6.6l2.2-2.2c.3-.3.7-.4 1-.2 1.1.4 2.3.6 3.6.6.6 0 1 .4 1 1V20c0 .6-.4 1-1 1A17 17 0 0 1 3 4c0-.6.4-1 1-1h3.5c.6 0 1 .4 1 1 0 1.3.2 2.5.6 3.6.1.3 0 .7-.2 1z"/></svg>
  <svg class="feature-icon" style="left:294px;top:398px" width="40" height="32" viewBox="0 0 30 24"><path fill="#e8262d" d="M11 2C5.5 2 1 5.4 1 9.6c0 2.2 1.2 4.1 3.2 5.5L3 19l4.6-2.4c1.1.3 2.2.4 3.4.4 5.5 0 10-3.4 10-7.4S16.5 2 11 2z"/><path fill="#e8262d" d="M23 8.5c.1.4.1.7.1 1.1 0 4.9-5 8.8-11.2 9 1.7 1.6 4.3 2.5 7.1 2.5.9 0 1.8-.1 2.7-.3L25.5 23l-.9-3.1C27.3 18.7 29 16.7 29 14.4c0-2.6-2.4-4.9-6-5.9z"/></svg>
  <svg class="feature-icon" style="left:370px;top:531px" width="36" height="36" viewBox="0 0 24 24"><circle cx="12" cy="12" r="10.5" fill="none" stroke="#e8262d" stroke-width="2"/><path fill="#e8262d" d="M12 6l5 5.5h-3.2V18h-3.6v-6.5H7z"/></svg>
  <svg class="feature-icon" style="left:817px;top:240px" width="38" height="38" viewBox="0 0 24 24"><circle cx="12" cy="12" r="11" fill="#e8262d"/><rect x="10.6" y="5" width="2.8" height="9" rx="1" fill="#fff"/><circle cx="12" cy="17.6" r="1.6" fill="#fff"/></svg>
  <svg class="feature-icon" style="left:870px;top:392px" width="30" height="42" viewBox="0 0 20 28"><path fill="#e8262d" d="M10 0C4.5 0 0 4.4 0 9.9 0 17 10 28 10 28s10-11 10-18.1C20 4.4 15.5 0 10 0zm0 14a4 4 0 1 1 0-8 4 4 0 0 1 0 8z"/></svg>
  <svg class="feature-icon" style="left:806px;top:520px" width="26" height="44" viewBox="0 0 16 28"><rect x="1" y="1" width="14" height="26" rx="2" fill="none" stroke="#e8262d" stroke-width="2"/><line x1="1" y1="5" x2="15" y2="5" stroke="#e8262d" stroke-width="1.6"/><line x1="1" y1="22" x2="15" y2="22" stroke="#e8262d" stroke-width="1.6"/><circle cx="8" cy="24.6" r="1.1" fill="#e8262d"/></svg>
</section>

<section class="reviews">
  <div class="reviews-bg" role="img" aria-label="Faint red-toned background photo of smiling seniors"></div>
  <h2 class="section-title">Customer Reviews</h2>
  <div class="title-rule"></div>
  <div class="review" style="left:110px">
    <div class="review-avatar" role="img" aria-label="Photo of a happy senior couple outdoors"></div>
    <p class="review-text">Nemo enim ipsam voluptatem quia voluptas sit aspernatur aut odit aut fugit, sed quia consequuntur magni dolores eos qui ratione voluptatem</p>
    <div class="review-name">Jane Roe - Korvelt</div>
    <div class="review-stars">★★★★★</div>
  </div>
  <div class="review" style="left:638px">
    <div class="review-avatar" role="img" aria-label="Photo of a smiling senior couple in a park"></div>
    <p class="review-text">Nemo enim ipsam voluptatem quia voluptas sit aspernatur aut odit aut fugit, sed quia consequuntur magni dolores eos qui ratione voluptatem</p>
    <div class="review-name">Jane Roe - Korvelt</div>
    <div class="review-stars">★★★★★</div>
  </div>
  <svg class="reviews-wave" width="1200" height="80" viewBox="0 0 1200 80" preserveAspectRatio="none">
    <path d="M0 8 C300 60 620 60 860 34 C1000 20 1120 12 1200 18 L1200 80 L0 80 Z" fill="#f2f2f2"/>
    <path d="M0 8 C300 60 620 60 860 34 C1000 20 1120 12 1200 18" fill="none" stroke="#ffffff" stroke-width="5"/>
    <path d="M0 26 C300 74 620 72 860 48 C1000 36 1120 30 1200 34" fill="none" stroke="#e8262d" stroke-width="3"/>
  </svg>
</section>

<footer class="site-footer">
  <div class="brand">Korvelt</div>
  <div class="social"><span></span><span></span><span></span><span></span></div>

  <div class="footer-col" style="left:307px">
    <h4>Contact us</h4>
    <ul class="contact-list">
      <li><svg width="13" height="17" viewBox="0 0 20 28"><path fill="#666" d="M10 0C4.5 0 0 4.4 0 9.9 0 17 10 28 10 28s10-11 10-18.1C20 4.4 15.5 0 10 0zm0 14a4 4 0 1 1 0-8 4 4 0 0 1 0 8z"/></svg><span>12 Lindenweg<br>CH-4417 Ermendorf, Switzerland</span></li>
      <li><svg width="15" height="15" viewBox="0 0 24 24"><path fill="#666" d="M6.6 10.8a15.1 15.1 0 0 0 6.6 6.6l2.2-2.2c.3-.3.7-.4 1-.2 1.1.4 2.3.6 3.6.6.6 0 1 .4 1 1V20c0 .6-.4 1-1 1A17 17 0 0 1 3 4c0-.6.4-1 1-1h3.5c.6 0 1 .4 1 1 0 1.3.2 2.5.6 3.6.1.3 0 .7-.2 1z"/></svg><span>Phone: 061-555-0192</span></li>
      <li><svg width="15" height="12" viewBox="0 0 24 18"><rect width="24" height="18" rx="2" fill="#666"/><path d="M2 3l10 7 10-7" fill="none" stroke="#f2f2f2" stroke-width="2"/></svg><span>Email: info@korvelt.example</span></li>
    </ul>
  </div>

  <div class="footer-col newsletter" style="left:612px">
    <h4>Sign up for newsletter</h4>
    <p>Excepteur sint occaecat cupidatat non proident, sunt in culpa qui officia deserunt</p>
    <div class="field">Enter email</div>
    <a class="btn" href="#">Sign up</a>
  </div>

  <div class="footer-col" style="left:969px">
    <h4>Quick links</h4>
    <ul class="quick-links">
      <li>Home</li><li>About</li><li>Services</li><li>Why Korvelt?</li><li>Blog</li><li>Contact</li>
    </ul>
  </div>
</footer>

<div class="copyright">© Copyright 2018 Korvelt GmbH. All Rights Reserved.</div>

</body>
</html>
```